Optometrist A5 flyer update 2014

We are an optical / optometrist business needing an existing A5 flyer updated. This flyer has been very successful but needs to be renewed.
We are supplying all the original source files including images.
I have included pdf files with annotations on the alteration we would like made.
We are open to suggestions / alterations to the design of the pamphlet.
We are after a modern design appealing to the various ages of our patient base.

```html
<!DOCTYPE html>
<html lang="en">
<head>
<meta charset="utf-8">
<title>Hollis Lane Optical – Flyer</title>
<link href="https://fonts.googleapis.com/css2?family=PT+Sans:wght@400;700&family=Open+Sans:wght@400;600;700&display=swap" rel="stylesheet">
<style>
  :root {
    --navy: #1f2a8a;
    --green: #1e9a2e;
    --lavender: #8e93c9;
    --white: #ffffff;
    --ink: #1a1a2e;
  }
  * { margin: 0; padding: 0; box-sizing: border-box; }
  html, body { width: 846px; height: 1200px; overflow: hidden; background: var(--white); }
  .flyer { position: relative; width: 846px; height: 1200px; overflow: hidden; font-family: "PT Sans", sans-serif; }

  .hero-photo {
    position: absolute; left: 0; top: 0; width: 846px; height: 870px;
    background:
      linear-gradient(180deg, #f3efe6 0%, #e6e3d2 12%, #b9c48f 24%, #8c9a5e 31%, #6f7358 37%, #8a7f76 42%, #9a93a8 47%, #8f93c6 55%, #8e93c9 100%);
  }

  .brand { position: absolute; left: 0; top: 46px; width: 846px; text-align: center; color: var(--navy); font-family: "PT Sans", sans-serif; font-weight: 400; line-height: 1; }
  .brand-line1 { display: block; font-size: 52px; }
  .brand-line2 { display: block; font-size: 74px; margin-top: 2px; }

  .tagline {
    position: absolute; left: 0; top: 448px; width: 846px; text-align: center;
    color: var(--white); font-family: "PT Sans", sans-serif; font-size: 50px; font-weight: 400;
    letter-spacing: -1px; text-shadow: 0 2px 4px rgba(0,0,0,0.35);
  }

  .services-panel {
    position: absolute; left: 52px; top: 522px; width: 759px; height: 325px;
    border: 1.5px solid rgba(255,255,255,0.85); background: rgba(255,255,255,0.28);
  }
  .panel-divider { position: absolute; left: 418px; top: 14px; width: 1.5px; height: 296px; background: rgba(255,255,255,0.8); }

  .exam-heading { position: absolute; left: 34px; top: 24px; font-size: 19px; font-weight: 700; color: var(--ink); }
  .exam-list { list-style: none; position: absolute; left: 28px; top: 67px; }
  .exam-list li {
    width: 363px; height: 40px; margin-bottom: 9px; padding-left: 42px;
    background: rgba(255,255,255,0.45); font-size: 20px; color: var(--ink);
    line-height: 40px; position: relative;
  }
  .exam-list li::before {
    content: ""; position: absolute; left: 15px; top: 15px; width: 11px; height: 11px; background: var(--navy);
  }

  .practice-info { position: absolute; left: 440px; top: 24px; width: 300px; color: var(--ink); }
  .practice-heading { font-size: 19px; font-weight: 700; }
  .practice-since { font-size: 17px; margin-top: 4px; }
  .feature-list { list-style: none; margin-top: 2px; }
  .feature-list li { position: relative; padding-left: 27px; font-size: 16.5px; line-height: 26px; }
  .feature-list li::before {
    content: ""; position: absolute; left: 2px; top: 8px; width: 10px; height: 10px; background: var(--navy);
  }

  .contact-area { position: absolute; left: 0; top: 870px; width: 846px; height: 330px; background: var(--white); }
  .optometrists-label { position: absolute; left: 0; top: 14px; width: 846px; text-align: center; font-family: "Open Sans", sans-serif; font-size: 21px; color: var(--navy); }
  .optometrists-names { position: absolute; left: 0; top: 44px; width: 846px; text-align: center; font-family: "Open Sans", sans-serif; font-size: 26px; font-weight: 700; color: var(--navy); }
  .optometrists-names .amp { color: var(--green); margin: 0 8px; }

  .contact-band { position: absolute; left: 0; top: 132px; width: 846px; height: 120px; background: var(--green); }
  .contact-icons { position: absolute; left: 323px; top: 84px; }
  .address { position: absolute; left: 0; top: 172px; width: 846px; text-align: center; font-family: "Open Sans", sans-serif; font-size: 21px; font-weight: 700; color: var(--white); }
  .phone { position: absolute; left: 0; top: 204px; width: 846px; text-align: center; font-family: "Open Sans", sans-serif; font-size: 32px; font-weight: 700; letter-spacing: 3px; color: var(--white); }
  .website { position: absolute; left: 0; top: 266px; width: 846px; text-align: center; font-family: "Open Sans", sans-serif; font-size: 24px; font-weight: 700; color: var(--navy); }
</style>
</head>
<body>
<div class="flyer">
  <div class="hero-photo" role="img" aria-label="Photograph of a pair of black-rimmed glasses on a table, with a sharp view of garden plants and a timber fence through the lenses and a soft blurred background"></div>

  <h1 class="brand">
    <span class="brand-line1">Hollis Lane</span>
    <span class="brand-line2">Optical</span>
  </h1>

  <h2 class="tagline">FOR ALL EYECARE NEEDS</h2>

  <section class="services-panel">
    <h3 class="exam-heading">NationCare bulk billed eye examination</h3>
    <ul class="exam-list">
      <li>Glaucoma assessment</li>
      <li>Diabetes vision assessment</li>
      <li>Cataract assessment</li>
      <li>Macula degeneration assessment</li>
      <li>Digital retinal photography</li>
    </ul>
    <div class="panel-divider"></div>
    <div class="practice-info">
      <h3 class="practice-heading">Independent Optometrists</h3>
      <p class="practice-since">Servicing Eastvale since 1989</p>
      <ul class="feature-list">
        <li>Over 500 spectacle frames and sunglasses to choose from</li>
        <li>Latest spectacle lens technology</li>
        <li>Contact lenses from all leading suppliers</li>
        <li>Direct billing to private health funds with ClaimPoint</li>
        <li>On site lens fittings to own frames</li>
      </ul>
    </div>
  </section>

  <section class="contact-area">
    <p class="optometrists-label">Optometrists:</p>
    <p class="optometrists-names">Marcus Delaine<span class="amp">&amp;</span>Nina Petrakos</p>

    <div class="contact-band"></div>

    <svg class="contact-icons" width="200" height="72" viewBox="0 0 200 72" aria-hidden="true">
      <path d="M0 48 Q0 6 34 6 H166 Q200 6 200 48 Z" fill="#ffffff"/>
      <g fill="#1f2a8a" stroke="#ffffff" stroke-width="3">
        <circle cx="34" cy="36" r="29"/>
        <circle cx="100" cy="36" r="29"/>
        <circle cx="166" cy="36" r="29"/>
      </g>
      <g fill="#ffffff">
        <path d="M34 19 L52 35 H47 V52 H38 V42 H30 V52 H21 V35 H16 Z"/>
        <path d="M93 20 Q88 22 88 30 Q90 44 104 52 Q110 54 113 49 L108 43 L103 46 Q96 41 94 33 L98 30 Z"/>
        <rect x="151" y="25" width="30" height="22" rx="2"/>
      </g>
      <path d="M152 27 L166 38 L180 27" fill="none" stroke="#1f2a8a" stroke-width="2.5"/>
    </svg>

    <p class="address">14b Hollis Lane, Eastbrook</p>
    <p class="phone">9555 0148</p>
    <p class="website">www.hollislaneoptical.com.au</p>
  </section>
</div>
</body>
</html>
```